Web page design for a startup, no coding

Quorvix is a Data mining startup helping companies get data from websites. We’re looking to revamp our website to make it more professional and conversation friendly.
I need a designer to design the website in PSD and Once the PSD is done, the HTML design will be awarded as a separate job. We’ll need continues improvements to the design based on the user behaviour in the site and this can be a long term work for the right designer.
Read the details on the attached document
Target Market(s)
Big data, Data Mining
Industry/Entity Type
Business Software
Number of Pages Required
5+ page
Requirements
Must have
- Refer to the doc
Nice to have
- Refer to the doc
Should not have
- Refer to the doc

```html
<!DOCTYPE html>
<html lang="en">
<head>
<meta charset="utf-8">
<title>Quorvix – Turn Websites into Structured Data Feeds</title>
<link href="https://fonts.googleapis.com/css2?family=Open+Sans:ital,wght@0,400;0,600;0,700;0,800;1,400;1,600&display=swap" rel="stylesheet">
<style>
:root{
  --orange:#f7941d;
  --orange-deep:#f07f0a;
  --orange-light:#ffa733;
  --ink:#333333;
  --body:#444444;
  --muted:#777777;
  --rule:#dddddd;
  --panel:#efefef;
  --night:#1d2731;
  --footer:#2d2d2d;
  --white:#ffffff;
}
*{box-sizing:border-box;margin:0;padding:0}
html,body{width:1200px;height:2956px;overflow:hidden}
body{font-family:"Open Sans",Arial,sans-serif;color:var(--body);background:var(--white);position:relative}
.abs{position:absolute}

/* hero */
.hero{position:absolute;left:0;top:0;width:1200px;height:670px;overflow:hidden}
.hero-photo{position:absolute;inset:0;background:
  radial-gradient(ellipse at 60% 45%,#6b6c6e 0%,#3d3b39 40%,#1e1c1a 75%),#222}
.hero-photo::after{content:"";position:absolute;left:0;right:0;bottom:0;height:230px;background:linear-gradient(180deg,rgba(90,62,36,0) 0%,rgba(92,64,38,.85) 100%)}
.logo{position:absolute;color:var(--white);font-weight:600;font-size:34px;letter-spacing:-.5px}
.nav{position:absolute;top:55px;right:57px;display:flex;gap:47px}
.nav a{color:var(--white);text-decoration:none;font-size:13px;font-weight:700;letter-spacing:.3px}
.nav a.active{color:var(--orange)}
.hero h1{position:absolute;top:262px;left:0;width:1200px;text-align:center;color:var(--white);font-size:43px;line-height:50px;font-weight:700;letter-spacing:1px}
.hero p{position:absolute;top:370px;left:0;width:1200px;text-align:center;color:var(--white);font-size:16px;line-height:30px;font-weight:600}
.btn{position:absolute;display:flex;align-items:center;justify-content:center;font-size:14px;font-weight:700;color:var(--white);letter-spacing:.3px}
.btn-solid{background:var(--orange)}
.dots{position:absolute;display:flex;gap:7px}
.dots i{display:block;width:11px;height:11px;border-radius:50%;background:var(--white)}
.dots i.on{background:var(--orange)}

/* testimonial */
.quote-band{position:absolute;top:670px;left:0;width:1200px;height:213px;background:var(--panel)}
.quote-side{position:absolute;left:0;top:0;width:331px;height:213px;background:var(--orange)}
.quote-side::after{content:"";position:absolute;right:-1px;top:90px;border-style:solid;border-width:18px 24px 18px 0;border-color:transparent var(--panel) transparent transparent}
.avatar{position:absolute;left:106px;top:27px;width:158px;height:158px;border-radius:50%;border:5px solid var(--white);background:radial-gradient(circle at 50% 40%,#d2d2d2,#8e8e8e)}
.quote-text{position:absolute;left:453px;top:693px;width:665px;font-style:italic;font-size:14.5px;line-height:31px;color:var(--ink)}
.quote-name{position:absolute;left:453px;top:792px;font-size:14.5px;font-weight:600;color:var(--orange)}
.dots.grey i{width:10px;height:10px;background:#c4c4c4}
.dots.grey i.on{background:#6a6a6a}

/* offerings */
.section-title{position:absolute;left:0;width:1200px;text-align:center;font-size:27px;font-weight:700;color:var(--ink);letter-spacing:.5px}
.lead{position:absolute;left:0;width:1200px;text-align:center;font-size:16px;line-height:28px;color:var(--body)}
.offer{position:absolute;width:330px;text-align:center}
.icon-ring{width:92px;height:92px;margin:0 auto;border-radius:50%;border:3px solid var(--orange);display:flex;align-items:center;justify-content:center}
.icon-ring.filled{background:var(--orange)}
.offer h3{margin-top:22px;font-size:17px;font-weight:700;color:var(--orange);letter-spacing:.5px}
.offer p{margin-top:9px;font-size:14.5px;line-height:28px;color:var(--body)}
.rule-h{position:absolute;height:1px;background:var(--rule)}
.rule-v{position:absolute;width:1px;background:var(--rule)}

/* why us */
.why{position:absolute;top:1718px;left:0;width:1200px;height:524px;background:
  radial-gradient(circle at 50% 52%,#3b4a57 0%,#26323d 40%,var(--night) 75%)}
.why .section-title{color:var(--white)}
.why .icon-ring{background:transparent}
.why .offer p{color:var(--white)}

/* contact */
.help{position:absolute;top:2242px;left:0;width:1200px;height:469px;background:
  linear-gradient(135deg,var(--orange-light) 0%,var(--orange) 45%,var(--orange-deep) 100%)}
.help h2{position:absolute;top:38px;left:0;width:1200px;text-align:center;color:var(--white);font-size:27px;font-weight:700;letter-spacing:.5px}
.help .lead{color:var(--white);top:92px;font-size:16px;line-height:30px}
.field{position:absolute;background:var(--white);font-size:12px;color:#777;padding:0 14px;display:flex;align-items:center}
.field.area{align-items:flex-start;padding-top:14px}
.btn-ghost{border:2px solid var(--white);font-size:12px}

/* footer */
.footer{position:absolute;top:2711px;left:0;width:1200px;height:245px;background:var(--footer)}
.footer .copy{position:absolute;left:75px;top:125px;font-size:12px;line-height:18px;color:#bbbbbb}
.social{position:absolute;left:75px;top:181px;display:flex;gap:11px}
.social i{display:block;width:22px;height:22px;border-radius:3px;background:#d8d8d8}
.f-col{position:absolute;top:52px}
.f-col h4{font-size:12px;font-weight:700;color:var(--orange);letter-spacing:.5px;margin-bottom:10px}
.f-col a{display:block;font-size:13px;line-height:32px;color:#cccccc;text-decoration:none}
.news-input{position:absolute;left:885px;top:84px;width:242px;height:44px;background:var(--white);font-size:12px;color:#777;display:flex;align-items:center;padding:0 14px}
</style>
</head>
<body>

<header class="hero">
  <div class="hero-photo" role="img" aria-label="Photo of an open laptop and a glass of water on a wooden desk"></div>
  <div class="logo" style="left:75px;top:38px">Quorvix</div>
  <nav class="nav">
    <a class="active" href="#">HOME</a><a href="#">SOLUTIONS</a><a href="#">PRICING</a><a href="#">COMPANY</a><a href="#">GET FREE QUOTE</a>
  </nav>
  <h1>TURN WEBSITES INTO STRUCTURED<br>DATA FEEDS</h1>
  <p>Easily get structured data feeds from any website through our cloud based data as a service platform.<br>No programming ,Servers or Expensive Softwares required.</p>
  <div class="btn btn-solid" style="left:498px;top:453px;width:205px;height:49px">GET FREE QUOTE</div>
  <div class="dots" style="left:566px;top:620px"><i class="on"></i><i></i><i></i><i></i></div>
</header>

<section class="quote-band">
  <div class="quote-side"><div class="avatar" role="img" aria-label="Portrait photo of the customer"></div></div>
  <svg class="abs" style="left:384px;top:30px" width="50" height="42" viewBox="0 0 50 42" aria-hidden="true">
    <path fill="#999" d="M0 42V24C0 10 6 2 20 0v8c-7 2-10 6-10 12h10v22zM28 42V24C28 10 34 2 48 0v8c-7 2-10 6-10 12h10v22z"/>
  </svg>
  <div class="dots grey" style="left:453px;top:172px"><i class="on"></i><i></i><i></i><i></i></div>
</section>
<p class="quote-text">“ My team had a tremendous task ahead of them as we needed to import over 5 thousand<br>products from our wholesale supplier’s website on to our local database. So website crawling and<br>data scraping was the logical path to take…”</p>
<p class="quote-name">-Marcus Fenwell @ tradelane.com</p>

<section>
  <h2 class="section-title" style="top:927px">OUR OFFERINGS</h2>
  <p class="lead" style="top:988px">Businesses of all sizes use our clean data feeds to Quickly build apps, Experiment with fresh ideas<br>and Solve business problems.</p>

  <div class="rule-v" style="left:420px;top:1075px;height:285px"></div>
  <div class="rule-v" style="left:780px;top:1075px;height:285px"></div>
  <div class="rule-h" style="left:75px;top:1372px;width:330px"></div>
  <div class="rule-h" style="left:435px;top:1372px;width:330px"></div>
  <div class="rule-h" style="left:795px;top:1372px;width:330px"></div>
  <div class="rule-v" style="left:420px;top:1388px;height:285px"></div>
  <div class="rule-v" style="left:780px;top:1388px;height:285px"></div>

  <div class="offer" style="left:75px;top:1077px">
    <div class="icon-ring filled"><svg width="30" height="28" viewBox="0 0 30 28" aria-hidden="true"><path fill="#fff" d="M0 2h5l1 3h22l-3 11H9l1 3h15v3H8L3 5H0z"/><circle cx="10" cy="25" r="2.5" fill="#fff"/><circle cx="23" cy="25" r="2.5" fill="#fff"/></svg></div>
    <h3>E-COMMERCE</h3>
    <p>Our Ecommerce product data feeds gives<br>you access to structured product<br>information like pricing,, Category,<br>reviews etc about your competitors.</p>
  </div>
  <div class="offer" style="left:435px;top:1077px">
    <div class="icon-ring"><svg width="36" height="30" viewBox="0 0 36 30" aria-hidden="true"><path d="M2 2v26h32" fill="none" stroke="#555" stroke-width="2.5"/><path d="M7 22l8-9 6 5 10-11" fill="none" stroke="#555" stroke-width="2.5"/></svg></div>
    <h3>LEAD GENERATION</h3>
    <p>We help find quality leads for your<br>business by extracting public data from<br>all kind of sources like Linkora,<br>FundBase, SeedRoster etc.</p>
  </div>
  <div class="offer" style="left:795px;top:1077px">
    <div class="icon-ring"><svg width="30" height="30" viewBox="0 0 30 30" aria-hidden="true"><circle cx="12" cy="12" r="8" fill="none" stroke="#555" stroke-width="3"/><path d="M18 18l9 9" stroke="#555" stroke-width="4" stroke-linecap="round"/></svg></div>
    <h3>SERP TRACKING</h3>
    <p>Our SERP data feeds gives companies<br>access to Search Engine rankings of any<br>keywords from search engines like<br>Searchly, Yondo and Bexa.</p>
  </div>

  <div class="offer" style="left:75px;top:1400px">
    <div class="icon-ring"><svg width="26" height="32" viewBox="0 0 26 32" aria-hidden="true"><path d="M2 2h15l7 7v21H2z" fill="#555"/><path d="M17 2v7h7" fill="#888"/><path d="M6 15h14M6 20h14M6 25h10" stroke="#fff" stroke-width="2"/></svg></div>
    <h3>NEWS AGGREGATION</h3>
    <p>We help businesses build their own<br>unique news data feeds by aggregating<br>data from news sites, industry<br>blogs etc..</p>
  </div>
  <div class="offer" style="left:435px;top:1400px">
    <div class="icon-ring"><svg width="36" height="34" viewBox="0 0 36 34" aria-hidden="true"><circle cx="14" cy="10" r="6" fill="#555"/><path d="M2 30c0-8 6-12 12-12s12 4 12 12z" fill="#555"/><circle cx="24" cy="20" r="6" fill="#fff" stroke="#555" stroke-width="2.5"/><path d="M28 24l6 6" stroke="#555" stroke-width="3" stroke-linecap="round"/></svg></div>
    <h3>RECRUITING</h3>
    <p>We help recruiters automate scouting<br>candidate profiles from different online<br>sources and speed up<br>hiring process.</p>
  </div>
  <div class="offer" style="left:795px;top:1400px">
    <div class="icon-ring"><svg width="22" height="36" viewBox="0 0 22 36" aria-hidden="true"><rect x="1.5" y="1.5" width="19" height="33" rx="3" fill="none" stroke="#555" stroke-width="2.5"/><path d="M5 7h12v19H5z" fill="#555"/><circle cx="11" cy="30" r="1.8" fill="#555"/></svg></div>
    <h3>BUILD YOUR APP</h3>
    <p>We help businesses quickly build their<br>apps on top of our scalable data<br>extraction infrastructure.</p>
  </div>
</section>

<section class="why" role="img" aria-label="Dark background photo of a glowing globe over a keyboard">
  <h2 class="section-title" style="top:53px">WHY US</h2>
  <div class="offer" style="left:75px;top:122px">
    <div class="icon-ring"><svg width="38" height="28" viewBox="0 0 38 28" aria-hidden="true"><rect x="6" y="2" width="26" height="18" rx="1" fill="none" stroke="#fff" stroke-width="2.5"/><path d="M1 24h36v2H1z" fill="#fff"/></svg></div>
    <h3>SOLVE REAL PROBLEMS</h3>
    <p>Quorvix provides a fully managed Big<br>Data As A Service .You can easily plug our<br>data feeds into your favourite tool and<br>start solving the real problems.</p>
  </div>
  <div class="offer" style="left:435px;top:122px">
    <div class="icon-ring"><svg width="38" height="34" viewBox="0 0 38 34" aria-hidden="true"><circle cx="14" cy="18" r="8" fill="none" stroke="#fff" stroke-width="6" stroke-dasharray="4 3"/><circle cx="14" cy="18" r="3" fill="#fff"/><circle cx="29" cy="8" r="5" fill="none" stroke="#fff" stroke-width="4" stroke-dasharray="3 2"/><circle cx="29" cy="27" r="4" fill="none" stroke="#fff" stroke-width="3.5" stroke-dasharray="3 2"/></svg></div>
    <h3>CLEAN DATA</h3>
    <p>We follow a strict quality assurance<br>process and a Machine learning<br>based Q&amp;A system to ensure the<br>data integrity.</p>
  </div>
  <div class="offer" style="left:795px;top:122px">
    <div class="icon-ring"><svg width="40" height="30" viewBox="0 0 40 30" aria-hidden="true"><circle cx="20" cy="8" r="6" fill="#fff"/><path d="M9 28c0-8 5-12 11-12s11 4 11 12z" fill="#fff"/><circle cx="7" cy="11" r="4" fill="#fff"/><path d="M0 25c0-5 3-8 7-8 2 0 3 1 4 1-2 2-3 5-3 7z" fill="#fff"/><circle cx="33" cy="11" r="4" fill="#fff"/><path d="M40 25c0-5-3-8-7-8-2 0-3 1-4 1 2 2 3 5 3 7z" fill="#fff"/></svg></div>
    <h3>CUSTOMER SUCCESS</h3>
    <p>Ensuring Customer success is our first<br>priority. Our customer success team<br>consists of experienced data mining<br>engineers and they are equipped with<br>modern tools .</p>
  </div>
  <div class="dots" style="left:584px;top:458px"><i class="on"></i><i></i></div>
</section>

<section class="help">
  <h2>WE’RE HERE TO HELP!</h2>
  <p class="lead">“ We’re friendly and available to help solve your data extraction problems. Fill the form below to contact us.<br>Let us do the heavy lifting for you.”</p>
  <div class="field" style="left:254px;top:177px;width:333px;height:44px">Enter Email Address</div>
  <div class="field" style="left:613px;top:177px;width:333px;height:44px;justify-content:space-between">Select Monthly Budget
    <svg width="10" height="6" viewBox="0 0 10 6" aria-hidden="true"><path d="M1 1l4 4 4-4" fill="none" stroke="#777" stroke-width="1.5"/></svg></div>
  <div class="field area" style="left:254px;top:232px;width:692px;height:111px">Drop us line or two, We will get back to you soon...</div>
  <div class="btn btn-ghost" style="left:496px;top:358px;width:207px;height:48px">SUBMIT MESSAGE</div>
</section>

<footer class="footer">
  <div class="logo" style="left:75px;top:64px;font-size:30px">Quorvix</div>
  <p class="copy">Copyright ©2016 Quorvix.<br>All Rights Reserved.</p>
  <div class="social" aria-label="Social links"><i></i><i></i><i></i><i></i><i></i></div>
  <div class="f-col" style="left:343px"><h4>SITE MAP</h4><a href="#">Solutions</a><a href="#">Pricing</a><a href="#">Company</a><a href="#">Get free Quote</a></div>
  <div class="f-col" style="left:544px"><h4>QUICK LINKS</h4><a href="#">Blog</a><a href="#">Startup Partner program</a><a href="#">Answers</a><a href="#">FAQ</a></div>
  <div class="f-col" style="left:743px"><h4>&nbsp;</h4><a href="#">Case Studies</a><a href="#">Careers</a><a href="#">Slide</a></div>
  <div class="f-col" style="left:885px"><h4>NEWSLETTER SIGN UP</h4></div>
  <div class="news-input">Enter Email Address</div>
  <div class="btn btn-solid" style="left:1036px;top:138px;width:91px;height:41px;font-size:12px">SIGN UP</div>
</footer>

</body>
</html>
```